We are a new company with 2 divisions a medical research and medical product sales. We need a company logo and Business Cards. The design files need to be provided to us in Adobe Photoshop CS 5.1.

Target Market(s)

Medical Community

Industry/Entity Type

Medical

Contact Information for Business Card

Company Name - Harrowgate Lifesciences LLC
Company Address 4127 Larkspur Ave Suite 7, Alder Hollow Fl 32614

Requirements
Must have
• The design files need to be provided to us in Adobe Photoshop CS 5.1.

```html
<!DOCTYPE html>
<html lang="en">
<head>
<meta charset="utf-8">
<title>Harrowgate Lifesciences LLC — Business Card</title>
<link rel="stylesheet" href="https://fonts.googleapis.com/css2?family=Sorts+Mill+Goudy&display=swap">
<style>
  :root {
    --page-bg: #e9ebee;
    --card-white: #ffffff;
    --brand-blue: #0b66b0;
    --brand-green: #1a9a3c;
    --ink-dark: #2a2a2a;
    --text-on-blue: #ffffff;
  }
  html, body {
    margin: 0;
    width: 1200px;
    height: 822px;
    overflow: hidden;
    background: var(--page-bg);
  }
  .canvas {
    position: relative;
    width: 1200px;
    height: 822px;
  }
  .business-card {
    position: absolute;
    left: 80px;
    top: 114px;
    width: 1040px;
    height: 594px;
    background: var(--card-white);
    overflow: hidden;
    box-shadow: 0 6px 22px rgba(0,0,0,0.18);
    font-family: "Sorts Mill Goudy", Georgia, serif;
  }
  .card-band {
    position: absolute;
    inset: 0;
  }
  .brand {
    position: absolute;
    left: 70px;
    top: 58px;
    display: flex;
    align-items: center;
    gap: 22px;
  }
  .brand-dot {
    width: 64px;
    height: 64px;
    border-radius: 50%;
    background: var(--brand-green);
  }
  .brand-name {
    margin: 0;
    font-weight: 400;
    font-size: 46px;
    line-height: 0.95;
    letter-spacing: 1px;
    text-transform: uppercase;
    color: var(--brand-blue);
  }
  .person {
    position: absolute;
    left: 70px;
    top: 250px;
    color: var(--ink-dark);
  }
  .person-name {
    margin: 0;
    font-size: 40px;
    font-weight: 400;
    line-height: 1;
  }
  .person-title {
    margin: 4px 0 0;
    font-size: 28px;
    line-height: 1;
  }
  .contact {
    position: absolute;
    right: 60px;
    bottom: 40px;
    margin: 0;
    text-align: right;
    font-style: normal;
    font-size: 30px;
    line-height: 1.12;
    color: var(--text-on-blue);
  }
  .contact span { display: block; }
</style>
</head>
<body>
<main class="canvas">
  <section class="business-card" aria-label="Business card front">
    <svg class="card-band" viewBox="0 0 1040 594" preserveAspectRatio="none" aria-hidden="true">
      <path d="M0 432 C 320 360, 700 300, 1040 205 L1040 594 L0 594 Z" fill="var(--brand-blue)"/>
    </svg>

    <header class="brand">
      <span class="brand-dot" aria-hidden="true"></span>
      <h1 class="brand-name">Harrowgate<br>Lifesciences LLC.</h1>
    </header>

    <div class="person">
      <p class="person-name">John Doe</p>
      <p class="person-title">Chief Executive Officer</p>
    </div>

    <address class="contact">
      <span>4127 Larkspur Ave Suite 7</span>
      <span>Alder Hollow Fl 32614</span>
      <span>Tel: 123 456 789</span>
      <span>Email: yourname@yourcompany.com</span>
      <span>www.yourcompany.com</span>
    </address>
  </section>
</main>
</body>
</html>
```